Halvery Construction Group Website

Need a dynamic corporate website that can be built on with time. We want to get our information out to the world and have a place where customers can submit requests for proposals.

Target Market(s)

Custom home owners and buyers. Architects and Real Estate Agents.

Industry/Entity Type

Construction

Number of Pages Required

3 page

Font styles to use
Serif
Sans Serif

Requirements
Must have
• Company logo, about, company contact information, biography, contact, projects,
• Sleek, modern, clean, attractive design.
• Online form customers can use for filling out a request for project proposal.
• Linkedin hyperlink.
• Uses www.halveryconstructiongroup.example

```html
<!DOCTYPE html>
<html lang="en">
<head>
<meta charset="utf-8">
<title>Halvery Construction Group, Inc.</title>
<link rel="stylesheet" href="https://fonts.googleapis.com/css2?family=Roboto+Condensed:wght@400;700&family=Open+Sans:wght@400;600;700&family=Raleway:wght@400;500&family=Lato:wght@700&display=swap">
<style>
:root{
  --blue:#0b53a0;
  --blue-deep:#1f3f8f;
  --blue-light:#3a9fd8;
  --footer:#0a4f9a;
  --grey-bar:#f4f4f4;
  --grey-band:#e8e8e8;
  --text:#555;
  --muted:#888;
  --white:#fff;
}
*{margin:0;padding:0;box-sizing:border-box}
html,body{width:1200px;height:2490px;overflow:hidden}
body{font-family:"Open Sans",sans-serif;color:var(--text);background:var(--white);position:relative}
section,header,footer,.topbar{position:absolute;left:0;width:1200px}
.abs{position:absolute}
.btn{position:absolute;background:var(--blue);color:var(--white);font-family:"Roboto Condensed",sans-serif;font-size:22px;display:flex;align-items:center;justify-content:center;border-radius:3px;text-decoration:none}

.topbar{top:0;height:42px;background:var(--grey-bar);border-bottom:1px solid #ddd}
.topbar .social{left:78px;top:10px;display:flex;align-items:center;gap:8px;color:var(--blue);font-size:16px}
.topbar .social i{width:18px;height:18px;background:var(--blue);display:block;border-radius:2px}
.topbar .phone{right:78px;top:4px;display:flex;align-items:center;gap:10px;color:var(--blue);font-family:"Roboto Condensed",sans-serif;font-weight:700;font-size:28px}

header{top:42px;height:113px;background:var(--white)}
.brand{left:78px;top:22px;display:flex;align-items:center;gap:14px}
.brand i{width:60px;height:60px;background:var(--blue-deep);display:block}
.brand span{font-family:"Roboto Condensed",sans-serif;font-weight:700;font-size:40px;color:var(--blue);letter-spacing:1px}
.nav{right:78px;top:28px;display:flex;gap:0;font-family:"Roboto Condensed",sans-serif;font-size:21px}
.nav a{color:var(--muted);text-decoration:none;padding:12px 24px;border-radius:3px}
.nav a.active{background:var(--blue);color:var(--white)}

.hero{top:155px;height:572px;background:linear-gradient(180deg,#c9d8df 0%,#9fb3bd 40%,#56606a 70%,#3a3d35 100%)}
.hero h1{right:80px;top:135px;text-align:right;font-family:"Lato",sans-serif;font-weight:700;font-size:42px;line-height:62px;color:var(--blue)}
.hero .btn{left:920px;top:277px;width:202px;height:56px;font-family:"Raleway",sans-serif;font-size:24px}

.welcome{top:727px;height:435px}
.welcome .mark{left:118px;top:115px;width:215px;height:200px;background:linear-gradient(180deg,var(--blue-deep),var(--blue-light));display:flex;align-items:center;justify-content:center;color:var(--white);font-family:"Open Sans",sans-serif;font-weight:700;font-size:30px}
.welcome .pre{left:382px;top:62px;font-family:"Roboto Condensed",sans-serif;font-size:25px;color:var(--muted)}
.welcome h2{left:382px;top:92px;font-family:"Roboto Condensed",sans-serif;font-weight:400;font-size:41px;color:var(--blue)}
.welcome p{left:382px;width:725px;font-size:15.5px;line-height:25px}
.welcome .btn{left:380px;top:327px;width:156px;height:46px}

.projects{top:1162px;height:601px;background:var(--grey-band)}
.projects h2{left:0;width:1200px;top:42px;text-align:center;font-family:"Raleway",sans-serif;font-weight:400;font-size:40px;color:var(--muted)}
.projects h2 span{color:var(--blue)}
.grid{left:78px;top:120px;width:1044px;display:grid;grid-template-columns:repeat(4,245px);grid-auto-rows:162px;gap:22px 21px}
.tile{display:block}
.tile.feature{display:flex;flex-direction:column;align-items:center;justify-content:center;text-align:center;color:var(--white);background:linear-gradient(180deg,#1e5fb0,#1552a0)}
.tile.feature strong{font-size:25px;margin-bottom:6px}
.tile.feature span{font-size:15px;line-height:24px;padding:0 18px}
.projects .btn{left:523px;top:501px;width:154px;height:47px;font-family:"Raleway",sans-serif}

.about{top:1763px;height:412px}
.about h2{left:78px;top:50px;font-family:"Roboto Condensed",sans-serif;font-weight:400;font-size:41px;color:var(--muted)}
.about h2 span{color:var(--blue)}
.about p{left:78px;width:610px;font-size:15.5px;line-height:25px}
.about .btn{left:78px;top:302px;width:156px;height:47px}
.video{left:739px;top:58px;width:385px;height:271px;background:linear-gradient(135deg,#6c7a86,#3e4650 60%,#2c3138)}
.video .play{left:163px;top:117px;width:52px;height:36px;background:#d8261c;border-radius:8px}
.video .play::after{content:"";position:absolute;left:21px;top:10px;border-left:14px solid var(--white);border-top:8px solid transparent;border-bottom:8px solid transparent}

footer{top:2175px;height:262px;background:var(--footer);color:var(--white)}
footer h3{font-family:"Roboto Condensed",sans-serif;font-weight:400;font-size:25px;margin-bottom:16px}
.fcol{position:absolute;top:30px;font-size:15px;line-height:24px}
.fcol.brandcol{left:78px;width:230px}
.fbrand{font-family:"Roboto Condensed",sans-serif;font-weight:700;font-size:28px;letter-spacing:1px;margin-bottom:20px;display:block}
.fsocial{display:flex;align-items:center;gap:12px;margin-top:16px}
.fsocial i{width:46px;height:46px;border-radius:50%;background:var(--white);display:block}
.fcol ul{list-style:none}
.fcol li{display:flex;align-items:center;gap:10px;font-size:17px;line-height:31px}
.fcol.links{left:350px}
.fcol.touch{left:621px;width:240px}
.touch .row{display:flex;gap:12px;align-items:flex-start;margin-bottom:10px;width:240px}
.touch .row span,.touch .row strong{min-width:0;flex:1;overflow-wrap:anywhere;word-break:break-all}
.touch .row span.addr{word-break:normal;overflow-wrap:normal}
.touch svg{flex:none;margin-top:4px}
.fcol.news{left:890px;width:234px}
.news input{display:block;width:234px;height:36px;border:0;background:var(--blue-light);color:var(--white);font-family:"Open Sans",sans-serif;font-size:15px;padding:0 7px;margin-top:12px}
.news input::placeholder{color:var(--white)}
.news button{display:block;margin-top:10px;width:141px;height:42px;border:0;border-radius:2px;background:var(--white);color:var(--blue);font-family:"Roboto Condensed",sans-serif;font-size:20px}
.copyright{position:absolute;left:0;top:2437px;width:1200px;height:53px;background:var(--blue-light);color:var(--white);text-align:center;font-size:14px;line-height:53px}
</style>
</head>
<body>

<div class="topbar">
  <a class="abs social"><i></i>ProNet</a>
  <div class="abs phone">
    <svg width="24" height="24" viewBox="0 0 24 24"><path fill="currentColor" d="M6.6 10.8a15.2 15.2 0 0 0 6.6 6.6l2.2-2.2c.3-.3.7-.4 1-.2 1.1.4 2.3.6 3.6.6.6 0 1 .4 1 1V20c0 .6-.4 1-1 1A17 17 0 0 1 3 4c0-.6.4-1 1-1h3.5c.6 0 1 .4 1 1 0 1.3.2 2.5.6 3.6.1.3 0 .7-.2 1z"/></svg>
    123 456 7890
  </div>
</div>

<header>
  <div class="abs brand"><i></i><span>HALVERY</span></div>
  <nav class="abs nav">
    <a class="active">HOME</a><a>ABOUT</a><a>PROJECTS</a><a>NEWS</a><a>CONTACT</a>
  </nav>
</header>

<section class="hero" role="img" aria-label="Modern single-storey glass house on a timber deck at dusk">
  <h1 class="abs">LOREM IPSUM IS SIMPLY<br>SUMMY TEXT AND PRINTING.</h1>
  <a class="btn">CONTACT US</a>
</section>

<section class="welcome">
  <div class="abs mark">HALVERY</div>
  <div class="abs pre">WELCOME TO</div>
  <h2 class="abs">HALVERY CONSTRUCTION GROUP, INC.</h2>
  <p class="abs" style="top:160px">Lorem Ipsum is simply dummy text of the printing and typesetting industry. Lorem Ipsum has been the industry's standard dummy text ever since the 1500s, when an unknown printer took a galley of type and scrambled it to make a type specimen book, It has survived not only five centuries.</p>
  <p class="abs" style="top:260px">Lorem Ipsum is simply dummy text of the printing and typesetting industry. Lorem Ipsum has been the industry's standard dummy text.</p>
  <a class="btn">READ MORE</a>
</section>

<section class="projects">
  <h2 class="abs">LATEST <span>PROJECT</span></h2>
  <div class="abs grid">
    <div class="tile" role="img" aria-label="Bright white living room interior" style="background:linear-gradient(135deg,#eceae6,#cfcac2)"></div>
    <div class="tile feature"><strong>Project title</strong><span>Lorem Ipsum is simply dummy text of the printing and typesetting industry.</span></div>
    <div class="tile" role="img" aria-label="Crane over a building site under blue sky" style="background:linear-gradient(180deg,#3d7fc4,#8fb9dc 60%,#b89a6a)"></div>
    <div class="tile" role="img" aria-label="Glass-walled modern office interior" style="background:linear-gradient(135deg,#e4e8ea,#9fb0b8)"></div>
    <div class="tile" role="img" aria-label="Modern glass house on a grassy hill" style="background:linear-gradient(180deg,#c7d5dc,#8f9ea6 60%,#4a5040)"></div>
    <div class="tile" role="img" aria-label="Glass-walled modern office interior" style="background:linear-gradient(135deg,#e9eced,#a4b4bb)"></div>
    <div class="tile" role="img" aria-label="Two-storey white house with red roof" style="background:linear-gradient(180deg,#4d8fd0,#b8d2e8 55%,#d8d4cc)"></div>
    <div class="tile" role="img" aria-label="Street of suburban houses with lawns" style="background:linear-gradient(180deg,#3f86cf,#9ab4c8 50%,#5f8f3e)"></div>
  </div>
  <a class="btn">VIEW ALL</a>
</section>

<section class="about">
  <h2 class="abs">ABOUT <span>US</span></h2>
  <p class="abs" style="top:110px">Lorem Ipsum is simply dummy text of the printing and typesetting industry. Lorem Ipsum has been the industry's standard dummy text ever since the 1500s, when an unknown printer took a galley of type and scrambled it to make a type specimen book, It has survived not only five centuries.</p>
  <p class="abs" style="top:235px">Lorem Ipsum is simply dummy text of the printing and typesetting industry. Lorem Ipsum has been the industry's standard dummy text.</p>
  <a class="btn">READ MORE</a>
  <div class="abs video" role="img" aria-label="Video of a business meeting in a glass office">
    <div class="abs play"></div>
  </div>
</section>

<footer>
  <div class="fcol brandcol">
    <span class="fbrand">HALVERY</span>
    Lorem Ipsum is simply dummy text of the printing and type setting industry.
    <div class="fsocial"><i></i>ProNet</div>
  </div>
  <div class="fcol links">
    <h3>Useful Links</h3>
    <ul>
      <li><svg width="10" height="14" viewBox="0 0 10 14"><path d="M2 1l6 6-6 6" fill="none" stroke="#fff" stroke-width="2.5"/></svg>Home</li>
      <li><svg width="10" height="14" viewBox="0 0 10 14"><path d="M2 1l6 6-6 6" fill="none" stroke="#fff" stroke-width="2.5"/></svg>About</li>
      <li><svg width="10" height="14" viewBox="0 0 10 14"><path d="M2 1l6 6-6 6" fill="none" stroke="#fff" stroke-width="2.5"/></svg>Projects</li>
      <li><svg width="10" height="14" viewBox="0 0 10 14"><path d="M2 1l6 6-6 6" fill="none" stroke="#fff" stroke-width="2.5"/></svg>News</li>
      <li><svg width="10" height="14" viewBox="0 0 10 14"><path d="M2 1l6 6-6 6" fill="none" stroke="#fff" stroke-width="2.5"/></svg>Contact</li>
    </ul>
  </div>
  <div class="fcol touch">
    <h3>Get In Touch</h3>
    <div class="row"><svg width="14" height="20" viewBox="0 0 14 20"><path fill="#fff" d="M7 0a7 7 0 0 0-7 7c0 5 7 13 7 13s7-8 7-13a7 7 0 0 0-7-7zm0 10a3 3 0 1 1 0-6 3 3 0 0 1 0 6z"/></svg><span class="addr">Lorem Ipsum is dummy text of the printing.</span></div>
    <div class="row"><svg width="16" height="16" viewBox="0 0 24 24"><path fill="#fff" d="M6.6 10.8a15.2 15.2 0 0 0 6.6 6.6l2.2-2.2c.3-.3.7-.4 1-.2 1.1.4 2.3.6 3.6.6.6 0 1 .4 1 1V20c0 .6-.4 1-1 1A17 17 0 0 1 3 4c0-.6.4-1 1-1h3.5c.6 0 1 .4 1 1 0 1.3.2 2.5.6 3.6.1.3 0 .7-.2 1z"/></svg><strong>123 456 7890</strong></div>
    <div class="row"><svg width="18" height="14" viewBox="0 0 18 14"><rect x="1" y="1" width="16" height="12" fill="none" stroke="#fff" stroke-width="1.6"/><path d="M1 1l8 7 8-7" fill="none" stroke="#fff" stroke-width="1.6"/></svg><span>info@halveryconstructiongroup.example</span></div>
  </div>
  <div class="fcol news">
    <h3>Newsletter</h3>
    Subscribe to stay on HALVERY CONSTRUCTION GROUP, INC.
    <input type="email" placeholder="Enter Email Id">
    <button>SUBSCRIBE</button>
  </div>
</footer>
<div class="copyright">© <strong>HALVERY CONSTRUCTION GROUP, INC.</strong> - 2016. All Rights Reserved.</div>

</body>
</html>
```